Navoro & Omvar Automotive Repair Shop. Need a new website design.

We specialize in Navoro & Omvar auto repair, but also work on other Asian import vehicles. We have been in business for 7 years and pride ourselves on high quality auto repair that is fixed right the first time. Would like the automotive repair website to incorporate the colors black, red and white if possible and have our logo and some Navoro and Omvar vehicles included in the website.

Target Market(s)

Navoro & Omvar vehicle owners

Industry/Entity Type

Automotive Repair

Coding

Coded - Design and coding required

Number of Pages Required

5+ page

Colors
EB3D1F
EC4F4E
F09395
F8D3D4
FCEDEE

Requirements
Must have
• Home, Services, Contact Us, Schedule appointment, and a gallery tab that I can add shop pictures to when completed.
Nice to have
• Would like to see example pictures of job next to each service listed.
Should not have
• Service not related to auto repair. Ex. auto detailing, towing, car wash

```html
<!DOCTYPE html>
<html lang="en">
<head>
<meta charset="utf-8">
<title>Kestrel Automotive – Landing Page Mobile View</title>
<link href="https://fonts.googleapis.com/css2?family=Lato:wght@400;700&display=swap" rel="stylesheet">
<style>
:root{
  --board:#555559;
  --screen:#1e1e21;
  --white:#ffffff;
  --red:#e0283f;
  --muted:#cfcfd3;
  --field-text:#444;
}
*{box-sizing:border-box;margin:0;padding:0}
html,body{width:1200px;height:863px;overflow:hidden}
body{background:var(--board);font-family:'Lato',sans-serif;color:var(--white);position:relative}
.brand-mark{position:absolute;left:297px;top:66px;width:170px;display:flex;flex-direction:column;align-items:center;gap:8px;font-weight:700;font-size:28px;line-height:30px;color:var(--white);text-align:center}
.brand-mark .dot{width:20px;height:20px;border-radius:50%;background:var(--red)}
.board-title{position:absolute;left:500px;top:96px;font-size:35px;font-weight:700;letter-spacing:-.2px;white-space:nowrap}
.phone{position:absolute;width:211px;border:4px solid var(--white);border-radius:27px;background:var(--screen);overflow:hidden}
.abs{position:absolute}
.p1{left:39px;top:255px;height:582px}
.p2{left:267px;top:286px;height:551px}
.p3{left:495px;top:209px;height:628px;background:var(--white)}
.p4{left:723px;top:325px;height:512px}
.p5{left:950px;top:274px;height:563px}

/* screen 1 */
.mini-brand{left:14px;top:18px;font-size:8px;font-weight:700;display:flex;align-items:center;gap:3px}
.mini-brand i{width:7px;height:7px;border-radius:50%;background:var(--red);display:block}
.menu{left:174px;top:24px;width:13px}
.menu span{display:block;height:1.5px;background:var(--white);margin-bottom:3px}
.hero-photo{left:0;top:58px;width:203px;height:334px;background:linear-gradient(180deg,#2a2a2d 0%,#5a5a5e 45%,#3b3b3e 75%,#1e1e21 100%)}
.hero-title{left:0;top:74px;width:203px;text-align:center;font-size:20px;font-weight:700;line-height:23px}
.hero-sub{left:0;top:179px;width:203px;text-align:center;font-size:10.5px;font-weight:700;line-height:13px}
.installer{left:13px;top:256px;font-size:8px}
.badge{background:#d9d9dc;border-radius:3px}
.badge.round{border-radius:50%;background:#2a7bd1}
.intro{left:10px;top:446px;width:183px;text-align:center;font-size:13px;line-height:15.6px}

/* screen 2 */
.copy{left:13px;width:178px;font-size:8.2px;line-height:10.2px}
.car-photo{left:13px;top:203px;width:176px;height:112px;background:linear-gradient(90deg,#ffffff 0%,#f0f0f1 55%,#9a9a9e 86%,#a8a8ab 100%)}
.dots{left:65px;top:332px;height:2px;width:71px;background:#6a6a6e}
.dots b{display:block;width:17px;height:2px;background:var(--red)}
.makes{left:10px;top:390px;width:183px;text-align:center;font-size:10.7px;line-height:12.8px}
.make{top:456px;width:64px;height:36px;background:var(--white);color:#111;font-size:8px;font-weight:700;display:flex;align-items:center;justify-content:center}
.chev{top:468px}

/* screen 3 */
.services-panel{left:0;top:0;width:203px;height:566px;background:linear-gradient(160deg,#2b2b2f 0%,#1b1b1e 50%,#26262a 100%)}
.services-title{left:0;top:34px;width:203px;text-align:center;font-size:13px;font-weight:700}
.service-list{left:14px;top:62px;list-style:none;display:flex;flex-direction:column;gap:9.7px;width:184px}
.service-list li{display:flex;align-items:center;gap:8px;font-size:8.3px;line-height:10px}
.service-list svg{flex:none}
.missing{left:0;top:583px;width:203px;text-align:center;font-size:10.7px;color:#222;line-height:13px}
.missing u{text-underline-offset:2px}

/* screen 4 */
.contact-h{left:13px;top:49px;font-size:12.8px;font-weight:700}
.contact-p{left:13px;top:75px;width:178px;font-size:10.7px;line-height:12.8px}
.appt{left:13px;top:150px;font-size:10.7px;font-weight:700}
.click{left:13px;top:172px;font-size:10.7px;color:var(--red);text-decoration:underline;text-underline-offset:2px}
.field{background:var(--white);color:var(--field-text);font-size:7px;padding-left:9px;display:flex;align-items:center;justify-content:space-between;padding-right:9px;height:26px}
.field.tall{align-items:flex-start;padding-top:10px;height:64px}
.submit{left:13px;top:428px;width:176px;height:27px;background:var(--red);font-size:8px;display:flex;align-items:center;justify-content:center}

/* screen 5 */
.gallery-top{left:0;top:0;width:203px;height:85px;background:var(--white)}
.gallery-title{left:0;top:17px;width:108px;text-align:center;font-size:13px;font-weight:700;color:#111}
.view-more{left:17px;top:37px;width:76px;height:21px;background:var(--red);font-size:8px;display:flex;align-items:center;justify-content:center;gap:5px}
.footer-bg{left:0;top:85px;width:203px;height:480px;background:linear-gradient(160deg,#2a2a2e 0%,#1a1a1d 55%,#232327 100%)}
.foot-brand{left:14px;top:226px;font-size:11px;font-weight:700;display:flex;align-items:center;gap:5px}
.foot-brand i{width:10px;height:10px;border-radius:50%;background:var(--red);display:block}
.copyright{left:14px;top:282px;font-size:7px}
.info{left:14px;display:flex;gap:6px;font-size:8px;line-height:10px;width:160px}
.info svg{flex:none;margin-top:1px}
.quick{left:14px;top:424px;font-size:8px;font-weight:700;border-bottom:1px solid var(--white);padding-bottom:1px}
.links{left:14px;top:444px;list-style:none;font-size:8px;line-height:18.8px}
</style>
</head>
<body>

<div class="brand-mark"><span class="dot"></span><span>Kestrel<br>Automotive</span></div>
<h1 class="board-title">Landing Page Mobile View</h1>

<!-- Home -->
<section class="phone p1">
  <div class="abs hero-photo" role="img" aria-label="Close-up photo of an engine cover"></div>
  <div class="abs mini-brand"><i></i>Kestrel</div>
  <div class="abs menu"><span></span><span></span><span></span></div>
  <h2 class="abs hero-title">“DEALERSHIP<br>QUALITY AT<br>AFFORDABLE<br>PRICES"</h2>
  <p class="abs hero-sub">Specializing in Navoro, Omvar, &amp; Virel<br>Auto Repair</p>
  <p class="abs installer">Authorized installer for</p>
  <div class="abs badge" style="left:13px;top:272px;width:48px;height:30px"></div>
  <div class="abs badge" style="left:72px;top:282px;width:40px;height:12px"></div>
  <div class="abs badge" style="left:13px;top:323px;width:34px;height:34px"></div>
  <div class="abs badge round" style="left:56px;top:325px;width:30px;height:30px"></div>
  <p class="abs intro">Kestrel Automotive is a locally owned and operated auto repair shop in Brookfield that offers comprehensive car care and services for Navoro &amp; Omvar and all other Asian imports vehicles.</p>
</section>

<!-- About -->
<section class="phone p2">
  <p class="abs copy" style="top:27px">Led by an AutoCert master certified technician with 20 years experience working for Navoro &amp; Omvar dealerships, our auto shop is your go to facility for everything from factory auto maintenance, including oil changes, fluid services and tune ups, to complex engine repairs, hybrid diagnostic &amp; repair, brake jobs, etc.</p>
  <p class="abs copy" style="top:118px">We have state of the art equipment and tools to ensure that we can properly diagnose and repair your vehicle to get you back on the road quickly. Our work comes with a warranty and we offer towing if needed. We also offer discounts for RideGo &amp; Hailly rides.</p>
  <div class="abs car-photo" role="img" aria-label="Photo of a dark grey Omvar sedan on a white background"></div>
  <svg class="abs" style="left:162px;top:253px" width="8" height="10" viewBox="0 0 8 10"><path d="M2 1l4 4-4 4" fill="none" stroke="#fff" stroke-width="1.4"/></svg>
  <div class="abs dots"><b></b></div>
  <p class="abs makes">Kestrel Automotive specializes in Navoro &amp; Omvar auto repair but also service and repair the following makes:</p>
  <svg class="abs chev" style="left:17px" width="8" height="12" viewBox="0 0 8 12"><path d="M6 1L1 6l5 5" fill="none" stroke="#fff" stroke-width="1.5"/></svg>
  <div class="abs make" style="left:35px">HARLEN</div>
  <div class="abs make" style="left:103px">CORVIA</div>
  <svg class="abs chev" style="left:175px" width="8" height="12" viewBox="0 0 8 12"><path d="M2 1l5 5-5 5" fill="none" stroke="#fff" stroke-width="1.5"/></svg>
</section>

<!-- Services -->
<section class="phone p3">
  <div class="abs services-panel" role="img" aria-label="Dark textured tire tread background"></div>
  <h2 class="abs services-title">Services</h2>
  <ul class="abs service-list">
    <li><svg width="9" height="9" viewBox="0 0 10 10"><rect x="0.7" y="0.7" width="8.6" height="8.6" fill="none" stroke="#e0283f" stroke-width="1.2"/><path d="M2.5 5l2 2 4-5" fill="none" stroke="#e0283f" stroke-width="1.2"/></svg>Automatic, Manual, Computerized Transmission Service &amp; Repair</li>
    <li><svg width="9" height="9" viewBox="0 0 10 10"><rect x="0.7" y="0.7" width="8.6" height="8.6" fill="none" stroke="#e0283f" stroke-width="1.2"/><path d="M2.5 5l2 2 4-5" fill="none" stroke="#e0283f" stroke-width="1.2"/></svg>Brakes Service &amp; Repair</li>
    <li><svg width="9" height="9" viewBox="0 0 10 10"><rect x="0.7" y="0.7" width="8.6" height="8.6" fill="none" stroke="#e0283f" stroke-width="1.2"/><path d="M2.5 5l2 2 4-5" fill="none" stroke="#e0283f" stroke-width="1.2"/></svg>Clutch Service &amp; Repair</li>
    <li><svg width="9" height="9" viewBox="0 0 10 10"><rect x="0.7" y="0.7" width="8.6" height="8.6" fill="none" stroke="#e0283f" stroke-width="1.2"/><path d="M2.5 5l2 2 4-5" fill="none" stroke="#e0283f" stroke-width="1.2"/></svg>Computer Diagnostics</li>
    <li><svg width="9" height="9" viewBox="0 0 10 10"><rect x="0.7" y="0.7" width="8.6" height="8.6" fill="none" stroke="#e0283f" stroke-width="1.2"/><path d="M2.5 5l2 2 4-5" fill="none" stroke="#e0283f" stroke-width="1.2"/></svg>CV Axle Service &amp; Repair</li>
    <li><svg width="9" height="9" viewBox="0 0 10 10"><rect x="0.7" y="0.7" width="8.6" height="8.6" fill="none" stroke="#e0283f" stroke-width="1.2"/><path d="M2.5 5l2 2 4-5" fill="none" stroke="#e0283f" stroke-width="1.2"/></svg>Electrical Specialists</li>
    <li><svg width="9" height="9" viewBox="0 0 10 10"><rect x="0.7" y="0.7" width="8.6" height="8.6" fill="none" stroke="#e0283f" stroke-width="1.2"/><path d="M2.5 5l2 2 4-5" fill="none" stroke="#e0283f" stroke-width="1.2"/></svg>Emission Repair &amp; Catalytic Converters</li>
    <li><svg width="9" height="9" viewBox="0 0 10 10"><rect x="0.7" y="0.7" width="8.6" height="8.6" fill="none" stroke="#e0283f" stroke-width="1.2"/><path d="M2.5 5l2 2 4-5" fill="none" stroke="#e0283f" stroke-width="1.2"/></svg>Engine Repair</li>
    <li><svg width="9" height="9" viewBox="0 0 10 10"><rect x="0.7" y="0.7" width="8.6" height="8.6" fill="none" stroke="#e0283f" stroke-width="1.2"/><path d="M2.5 5l2 2 4-5" fill="none" stroke="#e0283f" stroke-width="1.2"/></svg>Exhaust, Muffler Service &amp; Repair</li>
    <li><svg width="9" height="9" viewBox="0 0 10 10"><rect x="0.7" y="0.7" width="8.6" height="8.6" fill="none" stroke="#e0283f" stroke-width="1.2"/><path d="M2.5 5l2 2 4-5" fill="none" stroke="#e0283f" stroke-width="1.2"/></svg>Fuel Injection System Service, Cleaning &amp; Repair</li>
    <li><svg width="9" height="9" viewBox="0 0 10 10"><rect x="0.7" y="0.7" width="8.6" height="8.6" fill="none" stroke="#e0283f" stroke-width="1.2"/><path d="M2.5 5l2 2 4-5" fill="none" stroke="#e0283f" stroke-width="1.2"/></svg>Heating &amp; AC Repair</li>
    <li><svg width="9" height="9" viewBox="0 0 10 10"><rect x="0.7" y="0.7" width="8.6" height="8.6" fill="none" stroke="#e0283f" stroke-width="1.2"/><path d="M2.5 5l2 2 4-5" fill="none" stroke="#e0283f" stroke-width="1.2"/></svg>Hybrid Vehicle diagnostic &amp; repair</li>
    <li><svg width="9" height="9" viewBox="0 0 10 10"><rect x="0.7" y="0.7" width="8.6" height="8.6" fill="none" stroke="#e0283f" stroke-width="1.2"/><path d="M2.5 5l2 2 4-5" fill="none" stroke="#e0283f" stroke-width="1.2"/></svg>Insurance Claims</li>
    <li><svg width="9" height="9" viewBox="0 0 10 10"><rect x="0.7" y="0.7" width="8.6" height="8.6" fill="none" stroke="#e0283f" stroke-width="1.2"/><path d="M2.5 5l2 2 4-5" fill="none" stroke="#e0283f" stroke-width="1.2"/></svg>Leveling Kits &amp; Minor Lift Kit installation</li>
    <li><svg width="9" height="9" viewBox="0 0 10 10"><rect x="0.7" y="0.7" width="8.6" height="8.6" fill="none" stroke="#e0283f" stroke-width="1.2"/><path d="M2.5 5l2 2 4-5" fill="none" stroke="#e0283f" stroke-width="1.2"/></svg>Oil Changes</li>
    <li><svg width="9" height="9" viewBox="0 0 10 10"><rect x="0.7" y="0.7" width="8.6" height="8.6" fill="none" stroke="#e0283f" stroke-width="1.2"/><path d="M2.5 5l2 2 4-5" fill="none" stroke="#e0283f" stroke-width="1.2"/></svg>Pre Purchase Inspections</li>
    <li><svg width="9" height="9" viewBox="0 0 10 10"><rect x="0.7" y="0.7" width="8.6" height="8.6" fill="none" stroke="#e0283f" stroke-width="1.2"/><path d="M2.5 5l2 2 4-5" fill="none" stroke="#e0283f" stroke-width="1.2"/></svg>Radiators &amp; Fans Service &amp; Repair</li>
    <li><svg width="9" height="9" viewBox="0 0 10 10"><rect x="0.7" y="0.7" width="8.6" height="8.6" fill="none" stroke="#e0283f" stroke-width="1.2"/><path d="M2.5 5l2 2 4-5" fill="none" stroke="#e0283f" stroke-width="1.2"/></svg>State Inspection</li>
    <li><svg width="9" height="9" viewBox="0 0 10 10"><rect x="0.7" y="0.7" width="8.6" height="8.6" fill="none" stroke="#e0283f" stroke-width="1.2"/><path d="M2.5 5l2 2 4-5" fill="none" stroke="#e0283f" stroke-width="1.2"/></svg>Suspension Service &amp; Repair</li>
    <li><svg width="9" height="9" viewBox="0 0 10 10"><rect x="0.7" y="0.7" width="8.6" height="8.6" fill="none" stroke="#e0283f" stroke-width="1.2"/><path d="M2.5 5l2 2 4-5" fill="none" stroke="#e0283f" stroke-width="1.2"/></svg>Timing Belts &amp; Water Pumps</li>
    <li><svg width="9" height="9" viewBox="0 0 10 10"><rect x="0.7" y="0.7" width="8.6" height="8.6" fill="none" stroke="#e0283f" stroke-width="1.2"/><path d="M2.5 5l2 2 4-5" fill="none" stroke="#e0283f" stroke-width="1.2"/></svg>Tire Balance &amp; Rotations</li>
    <li><svg width="9" height="9" viewBox="0 0 10 10"><rect x="0.7" y="0.7" width="8.6" height="8.6" fill="none" stroke="#e0283f" stroke-width="1.2"/><path d="M2.5 5l2 2 4-5" fill="none" stroke="#e0283f" stroke-width="1.2"/></svg>Tires</li>
    <li><svg width="9" height="9" viewBox="0 0 10 10"><rect x="0.7" y="0.7" width="8.6" height="8.6" fill="none" stroke="#e0283f" stroke-width="1.2"/><path d="M2.5 5l2 2 4-5" fill="none" stroke="#e0283f" stroke-width="1.2"/></svg>Tune ups &amp; Factory Scheduled Maintenance</li>
    <li><svg width="9" height="9" viewBox="0 0 10 10"><rect x="0.7" y="0.7" width="8.6" height="8.6" fill="none" stroke="#e0283f" stroke-width="1.2"/><path d="M2.5 5l2 2 4-5" fill="none" stroke="#e0283f" stroke-width="1.2"/></svg>24-hr Night Drop</li>
  </ul>
  <p class="abs missing">Dont see a service you need?<br><u>Contact us</u></p>
</section>

<!-- Contact -->
<section class="phone p4">
  <h2 class="abs contact-h">Contact us for a free estimate!</h2>
  <p class="abs contact-p">Please include year, model, and the service or repair you would like an estimate on.</p>
  <p class="abs appt">Want to make appointment instead?</p>
  <p class="abs click">Click Here</p>
  <div class="abs field" style="left:13px;top:215px;width:176px">Name</div>
  <div class="abs field" style="left:13px;top:250px;width:84px">Email Address</div>
  <div class="abs field" style="left:105px;top:250px;width:84px">Phone</div>
  <div class="abs field" style="left:13px;top:285px;width:84px">Model<svg width="6" height="4" viewBox="0 0 6 4"><path d="M.5.5L3 3 5.5.5" fill="none" stroke="#444"/></svg></div>
  <div class="abs field" style="left:105px;top:285px;width:84px">Year<svg width="6" height="4" viewBox="0 0 6 4"><path d="M.5.5L3 3 5.5.5" fill="none" stroke="#444"/></svg></div>
  <div class="abs field" style="left:13px;top:320px;width:176px">Services<svg width="6" height="4" viewBox="0 0 6 4"><path d="M.5.5L3 3 5.5.5" fill="none" stroke="#444"/></svg></div>
  <div class="abs field tall" style="left:13px;top:355px;width:176px">Message</div>
  <div class="abs submit">Submit</div>
</section>

<!-- Gallery & footer -->
<section class="phone p5">
  <div class="abs gallery-top"></div>
  <h2 class="abs gallery-title">Gallery</h2>
  <div class="abs view-more">View More <svg width="8" height="6" viewBox="0 0 8 6"><path d="M0 3h7M4.5.5L7 3 4.5 5.5" fill="none" stroke="#fff" stroke-width="1.1"/></svg></div>
  <div class="abs footer-bg" role="img" aria-label="Dark textured tire tread background"></div>
  <div class="abs" style="left:115px;top:0;width:6px;height:85px;background:#1e1e21"></div>
  <div class="abs" role="img" aria-label="Photo of a white Navoro SUV" style="left:124px;top:4px;width:79px;height:75px;background:linear-gradient(160deg,#ffffff 0%,#d8d8da 60%,#8c8c90 100%)"></div>
  <div class="abs" role="img" aria-label="Photo of a Navoro V8 engine cover" style="left:0;top:88px;width:78px;height:80px;background:linear-gradient(160deg,#3a3a3d,#5c5c60 55%,#2b2b2e)"></div>
  <div class="abs" role="img" aria-label="Photo of a white Navoro pickup truck" style="left:86px;top:88px;width:117px;height:80px;background:linear-gradient(160deg,#ffffff 0%,#e6e6e8 55%,#a4a4a8 100%)"></div>
  <div class="abs foot-brand"><i></i>Kestrel Automotive</div>
  <p class="abs copyright">© 2017 Kestrel Automotive LLC</p>
  <div class="abs info" style="top:309px"><svg width="8" height="10" viewBox="0 0 8 10"><path d="M4 10S0 5.6 0 3.8a4 4 0 018 0C8 5.6 4 10 4 10z" fill="#fff"/><circle cx="4" cy="3.8" r="1.4" fill="#1e1e21"/></svg><span>418 Ridgeview Circle #5 Brookfield,<br>TX 75000</span></div>
  <div class="abs info" style="top:338px"><svg width="9" height="9" viewBox="0 0 10 10"><circle cx="5" cy="5" r="4.3" fill="none" stroke="#fff"/><path d="M5 2.5V5l1.8 1.2" fill="none" stroke="#fff"/></svg><span>Monday - Friday,<br>8:30 am - 6:00 pm</span></div>
  <div class="abs info" style="top:367px"><svg width="9" height="9" viewBox="0 0 10 10"><path d="M2 .5l2 2.2-1 1.3c.7 1.4 1.6 2.3 3 3l1.3-1 2.2 2L8.6 9.5C4.2 9.2.8 5.8.5 1.4z" fill="#fff"/></svg><span>Office: 555.013.4410<br>Cell: 555.019.2273</span></div>
  <div class="abs info" style="top:396px"><svg width="9" height="7" viewBox="0 0 10 8"><rect width="10" height="8" rx="1" fill="#fff"/><path d="M.5.8L5 4.5 9.5.8" fill="none" stroke="#1e1e21"/></svg><span>KestrelAutoLLC@example.com</span></div>
  <p class="abs quick">Quick Links</p>
  <ul class="abs links">
    <li>Home</li><li>Services</li><li>Contact Us</li><li>Gallery</li><li>Schedule an Appointment</li>
  </ul>
</section>

</body>
</html>
```